Beauty Therapy Web Design

I need a web page design for a small beauty therapy clinic, the owner is currently the only beauty therapist working there.
We require the following pages:
Home
About
Treatments
Nails
Courses
Contact
I will attach the clinics business card, treatment menu and signage so that you get a feeling for the branding colours etc.
This is the first website for the beauty therapist, she would like to attract new clients and also tourists that come in on the cruise ships. The thing that sets her apart from other clinics is that she welcomes texting for appointments.
I have selected refundable because I have never done this before so I don't know what to expect, I have the full intention of going through with it as long as I get a good design.
Feel free to ask for further information
Reason: Project extended as I am away for work and am unable to meet with the owner.
Target Market(s)
Females 18 to 50
Industry/Entity Type
Business
Look and feel

```html
<!DOCTYPE html>
<html lang="en">
<head>
<meta charset="utf-8">
<title>Nails – Lumina Beauty Therapy</title>
<link href="https://fonts.googleapis.com/css2?family=Carlito:wght@400;700&family=Cormorant+Garamond:ital,wght@1,500;1,600&display=swap" rel="stylesheet">
<style>
  :root {
    --purple: #6b5799;
    --purple-text: #6a53a0;
    --gold: #bf9c3f;
    --white: #ffffff;
  }
  * { box-sizing: border-box; margin: 0; padding: 0; }
  html, body { width: 1200px; height: 1200px; overflow: hidden; background: var(--white); }
  body { position: relative; font-family: "Carlito", "Calibri", sans-serif; color: var(--purple-text); }

  .site-header { position: absolute; left: 0; top: 0; width: 1200px; height: 203px; background: var(--purple); }
  .brand { position: absolute; left: 124px; top: 78px; color: var(--gold); font-family: "Carlito", "Calibri", sans-serif; font-weight: 400; font-size: 36px; line-height: 44px; white-space: nowrap; }
  .booking-line { position: absolute; right: 125px; top: 16px; font-family: "Cormorant Garamond", serif; font-style: italic; font-weight: 500; font-size: 22px; font-variant-numeric: lining-nums; color: var(--gold); white-space: nowrap; }
  .main-nav a { position: absolute; top: 150px; color: var(--white); text-decoration: none; font-size: 21px; line-height: 33px; white-space: nowrap; }
  .main-nav a.current { background: var(--gold); border-radius: 6px; width: 62px; text-align: center; }
  .nav-home { left: 566px; }
  .nav-about { left: 641px; }
  .nav-nails { left: 706px; }
  .nav-treatments { left: 787px; }
  .nav-courses { left: 912px; }
  .nav-contact { left: 1003px; }

  .page-title { position: absolute; left: 110px; top: 214px; font-family: "Cormorant Garamond", serif; font-style: italic; font-weight: 500; font-size: 32px; color: var(--gold); }
  .intro { position: absolute; left: 108px; top: 265px; font-size: 18px; white-space: nowrap; }

  .price-card { position: absolute; top: 319px; width: 295px; border: 3px solid var(--purple); border-radius: 0 0 3px 3px; }
  .price-card h2 { height: 40px; background: var(--purple); color: var(--gold); font-family: "Cormorant Garamond", serif; font-style: italic; font-weight: 600; font-size: 29px; line-height: 40px; padding-left: 3px; white-space: nowrap; }
  .price-body { display: flex; }
  .price-items, .price-values { font-weight: 700; font-size: 20px; line-height: 25px; padding: 11px 0 10px 3px; white-space: nowrap; }
  .price-items { width: 195px; border-right: 1px solid var(--purple); }
  .price-values { padding-left: 17px; }
  .pedicure { left: 107px; }
  .pedicure .price-body { height: 276px; }
  .manicure { left: 442px; }
  .manicure .price-items { width: 194px; }
  .manicure .price-body { height: 198px; }
  .enhancement { left: 774px; }
  .enhancement .price-items { width: 194px; }
  .enhancement .price-body { height: 182px; }

  .text-booking { position: absolute; left: 775px; top: 597px; width: 291px; height: 40px; background: var(--purple); color: var(--white); border-radius: 10px; font-size: 18px; line-height: 40px; padding-left: 8px; white-space: nowrap; }
  .divider { position: absolute; left: 108px; top: 675px; width: 951px; height: 1px; background: var(--purple); }

  .site-footer { position: absolute; left: 0; top: 1137px; width: 1200px; height: 63px; background: var(--purple); color: var(--white); font-size: 14.5px; }
  .footer-nav a { position: absolute; top: 22px; color: var(--white); text-decoration: none; white-space: nowrap; }
  .footer-nav a.current { color: var(--gold); text-decoration: underline; }
  .fn-home { left: 107px; }
  .fn-about { left: 160px; }
  .fn-nails { left: 215px; }
  .fn-treatments { left: 264px; }
  .fn-courses { left: 354px; }
  .fn-contact { left: 419px; }
  .copyright { position: absolute; right: 140px; top: 25px; white-space: nowrap; }
</style>
</head>
<body>
  <header class="site-header">
    <div class="brand">Lumina Beauty Therapy</div>
    <p class="booking-line">Book Your Treaments, Call or Text: 07 555 0142 / 027 555 0198</p>
    <nav class="main-nav">
      <a href="#" class="nav-home">Home</a>
      <a href="#" class="nav-about">About</a>
      <a href="#" class="nav-nails current">Nails</a>
      <a href="#" class="nav-treatments">Treatments</a>
      <a href="#" class="nav-courses">Courses</a>
      <a href="#" class="nav-contact">Contact</a>
    </nav>
  </header>

  <h1 class="page-title">Nails</h1>
  <p class="intro">We have a range of nail treatments availble including pedicures and manicures</p>

  <section class="price-card pedicure">
    <h2>Pedicure</h2>
    <div class="price-body">
      <div class="price-items">Classic - 45 min<br>Deluxe - 60 min<br>Spa Delux - 75 min<br>(Includes Paraffic Dip )<br>Nail Shape<br>Nail Paint<br>French Polish<br>Sen Citizens Nail Trea-<br>tment (Ladies &amp; Gentl-<br>emen)</div>
      <div class="price-values">$45.00<br>$60.00<br>$75.00<br>&nbsp;<br>$10.00<br>$10.00<br>$15.00<br>$25.00</div>
    </div>
  </section>

  <section class="price-card manicure">
    <h2>Manicure</h2>
    <div class="price-body">
      <div class="price-items">Classic - 45 min<br>Deluxe - 60 min<br>Spa Delux - 75 min<br>(Includes Paraffic Dip )<br>Nail Shape<br>Nail Paint<br>French Polish</div>
      <div class="price-values">$35.00<br>$50.00<br>$60.00<br>&nbsp;<br>$10.00<br>$10.00<br>$15.00</div>
    </div>
  </section>

  <section class="price-card enhancement">
    <h2>Nail Enhancement</h2>
    <div class="price-body">
      <div class="price-items">Acrylic or Gel Full Set<br>Pink Backfill<br>Pink &amp; White Backfill<br>Acrylic Toe Nails<br>Gel Toe Nails<br>Acrylic Nail Removal</div>
      <div class="price-values">$70.00<br>$40.00<br>$50.00<br>$65.00<br>$25.00<br>$40.00</div>
    </div>
  </section>

  <div class="text-booking">Book Treatment By Text: 07 555 0142</div>
  <div class="divider"></div>

  <footer class="site-footer">
    <nav class="footer-nav">
      <a href="#" class="fn-home">Home</a>
      <a href="#" class="fn-about">About</a>
      <a href="#" class="fn-nails current">Nails</a>
      <a href="#" class="fn-treatments">Treatments</a>
      <a href="#" class="fn-courses">Courses</a>
      <a href="#" class="fn-contact">Contact</a>
    </nav>
    <p class="copyright">© Copyright Lumina Beauty Therapy 2012</p>
  </footer>
</body>
</html>
```